Lumavento business card

We need a modern business card - With our 4 colors - See web: www.lumavento.dk

I have attached logo and som old business Cards we have - Lets Make the new ones shine...:-) -

Industry/Entity Type

Business

Requirements
Must have
• the logo with lumavento only,

```html
<!DOCTYPE html>
<html lang="da">
<head>
<meta charset="utf-8">
<title>Lumavento visitkort</title>
<link href="https://fonts.googleapis.com/css2?family=Open+Sans:wght@300;400;700&display=swap" rel="stylesheet">
<style>
  :root {
    --orange: #f2841f;
    --purple: #7a2a7c;
    --pink: #e5128c;
    --green: #a9c93a;
    --white: #ffffff;
    --ink: #3a3a3a;
    --backdrop: #151515;
  }
  html, body {
    margin: 0;
    width: 1200px;
    height: 900px;
    overflow: hidden;
    background: var(--backdrop);
    font-family: "Open Sans", Arial, sans-serif;
  }
  .stage { position: relative; width: 1200px; height: 900px; }
  .card {
    position: absolute;
    top: 306px;
    width: 440px;
    height: 271px;
    border-radius: 12px;
    overflow: hidden;
    background: var(--white);
  }
  .card--front { left: 149px; }
  .card--back { left: 608px; }
  .panel { position: absolute; }
  .panel--orange { left: 0; top: 0; width: 217px; height: 135px; background: var(--orange); }
  .panel--purple { left: 224px; top: 0; width: 216px; height: 135px; background: var(--purple); }
  .panel--pink { left: 0; top: 142px; width: 217px; height: 129px; background: var(--pink); }
  .panel--green { left: 224px; top: 142px; width: 216px; height: 129px; background: var(--green); }
  .person { position: absolute; left: 23px; top: 50px; color: var(--white); }
  .person__name { font-weight: 700; font-size: 16px; line-height: 20px; }
  .person__role { font-size: 11px; line-height: 16px; }
  .contact { position: absolute; left: 23px; top: 18px; color: var(--white); font-size: 12px; line-height: 16px; }
  .contact__address { margin: 0 0 8px; }
  .contact__line { display: flex; align-items: center; height: 18px; }
  .contact__icon { width: 9px; height: 9px; margin: 0 8px 0 2px; fill: var(--white); }
  .mark-spot {
    position: absolute; left: 78px; top: 37px; width: 60px; height: 60px;
    border: 2px solid var(--white); border-radius: 50%;
  }
  .brand { position: absolute; left: 0; width: 100%; text-align: center; color: var(--white); }
  .brand__name { top: 38px; font-weight: 300; font-size: 21px; letter-spacing: 3px; }
  .brand__tagline { top: 76px; font-weight: 300; font-size: 16px; }
  .back-art { position: absolute; left: 0; top: 0; }
  .back-brand { position: absolute; left: 0; width: 100%; text-align: center; color: var(--ink); }
  .back-brand__name { top: 154px; font-size: 17px; letter-spacing: 3px; font-weight: 400; }
  .back-brand__tagline { top: 198px; font-size: 12px; }
</style>
</head>
<body>
<div class="stage">
  <section class="card card--front">
    <div class="panel panel--orange">
      <div class="person">
        <div class="person__name">Mads Lindholm</div>
        <div class="person__role">Salgsdirektør</div>
      </div>
    </div>
    <div class="panel panel--purple">
      <div class="mark-spot"></div>
    </div>
    <div class="panel panel--pink">
      <div class="contact">
        <p class="contact__address">Kastanievej 14 - 2000<br>Frederiksberg -Tlf. 38 40 12 70</p>
        <div class="contact__line">
          <svg class="contact__icon" viewBox="0 0 10 10"><path d="M2 0.5 L3.6 2.6 L2.8 3.6 Q4 6 6.4 7.2 L7.4 6.4 L9.5 8 L8.4 9.5 Q3.5 9 0.5 1.6 Z"/></svg>+45 51 62 73 84
        </div>
        <div class="contact__line">
          <svg class="contact__icon" viewBox="0 0 10 10"><path d="M0 2 H10 V8.5 H0 Z M0.6 2.4 L5 5.6 L9.4 2.4" stroke="#e5128c" stroke-width="0.8"/></svg>ml@lumavento.dk
        </div>
        <div class="contact__line">
          <svg class="contact__icon" viewBox="0 0 10 10"><circle cx="5" cy="5" r="4.8"/><path d="M0.5 5 H9.5 M5 0.3 Q2.5 5 5 9.7 M5 0.3 Q7.5 5 5 9.7" stroke="#e5128c" stroke-width="0.7" fill="none"/></svg>www.lumavento.dk
        </div>
      </div>
    </div>
    <div class="panel panel--green">
      <div class="brand brand__name">lumavento</div>
      <div class="brand brand__tagline">Medier til unge</div>
    </div>
  </section>

  <section class="card card--back">
    <svg class="back-art" width="440" height="271" viewBox="0 0 440 271">
      <rect x="0" y="0" width="219" height="135" fill="var(--orange)"/>
      <rect x="224" y="0" width="216" height="135" fill="var(--purple)"/>
      <rect x="0" y="142" width="219" height="129" fill="var(--pink)"/>
      <rect x="224" y="142" width="216" height="129" fill="var(--green)"/>
      <circle cx="221" cy="139" r="122" fill="none" stroke="var(--white)" stroke-width="6"/>
      <circle cx="221" cy="139" r="111" fill="var(--white)"/>
      <circle cx="221" cy="110" r="9" fill="var(--green)"/>
      <line x1="132" y1="186" x2="309" y2="186" stroke="var(--green)" stroke-width="2"/>
    </svg>
    <div class="back-brand back-brand__name">lumavento</div>
    <div class="back-brand back-brand__tagline">Medier til unge</div>
  </section>
</div>
</body>
</html>
```